4D Cradle Glimpse Luxury Ultrasound Billboard

Design a HIGH-END, MODERN billboard for my private prenatal ultrasound studio, 4D Cradle Glimpse, located in Pace, Florida.
This billboard will be viewed by drivers traveling at highway speeds, so it must be extremely clean, simple, and readable within 6 seconds.
About My Business
4D Cradle Glimpse is a private prenatal ultrasound studio specializing in:
Highest technology 4D/HD Ultrasounds
Early Gender Determination
Pregnancy Confirmation
I have been serving families for nearly 10 years and is known for creating a memorable experience, not just an ultrasound appointment.
Design Style
I DO NOT want:
Flowers
Leaves
Swirls
Glitter
Hearts everywhere
Busy backgrounds
Generic maternity stock graphics
I DO want:
Modern
Luxury
Upscale
Clean
Professional
Eye-catching
Premium medical spa feel
Colors
Use colors from my logo:
LOGO Green ( or a deep green)
Black
White
Soft Gold accents
Images:
Incorporate my professional headshot in a clean, modern way, logo, and the ultrasound images
Text
Keep wording minimal.
Primary Headline ( OPEN TO IDEAS) :
EXAMPLES ( WOULD RATHER SOMETHING MORE CATCHY)
" ADVANCED IMAGING. UNFORGETTABLE MOMENTS"
"MEET YOUR BABY BEFORE BIRTH"
Under headline:
4D Ultrasound • Early Gender • Pregnancy Confirmation
Business Name:
4D Cradle Glimpse
Private Prenatal Ultrasound Studio
Phone Number:
850-471-5923
Important
This billboard must be readable in 5–6 seconds from a moving vehicle.
Less text is better.
The phone number and business name must be visible from a distance.
The design should feel like a premium brand that immediately tells expecting parents:
“This is where I go to see my baby.”
Files Provided
Official logo
Headshot
Ultrasound images
Don’t make this look like a medical office billboard.
Make it look like a luxury baby experience billboard. That’s what separates 4D Cradle Glimpse from hospitals, OB offices, and all the new studios popping up around you. The emotional connection is what gets moms to book. ❤️
Billboard Size - 10.6” x 36”

```html
<!DOCTYPE html>
<html lang="en">
<head>
<meta charset="utf-8">
<title>4D Cradle Glimpse — Billboard</title>
<link href="https://fonts.googleapis.com/css2?family=Cinzel:wght@600;700&family=Marcellus&display=swap" rel="stylesheet">
<style>
  :root {
    --gold: #c9a03c;
    --sage: #56625c;
    --ink: #141414;
    --paper: #ffffff;
    --backdrop: #e8e8e5;
    --frame: #5d6a64;
  }
  * { box-sizing: border-box; margin: 0; padding: 0; }
  html, body { width: 901px; height: 1200px; overflow: hidden; }
  body { background: var(--backdrop); position: relative; font-family: "Marcellus", serif; }

  .billboard {
    position: absolute; left: 20px; top: 474px;
    width: 861px; height: 251px;
    background: var(--paper);
    box-shadow: 0 10px 22px rgba(0,0,0,.25);
    overflow: hidden;
  }
  .headshot {
    position: absolute; left: 21px; top: 17px; width: 107px; height: 161px;
    background: linear-gradient(180deg, #e3c99a 0%, #d9b38c 40%, #3f5a3e 70%, #2f4a33 100%);
    border-radius: 50px 50px 0 0;
  }
  .headline {
    position: absolute; left: 149px; top: 12px;
    font-family: "Cinzel", serif; font-weight: 700; font-size: 50px; line-height: 47px;
    letter-spacing: -0.5px; white-space: nowrap;
  }
  .headline .line-gold { color: var(--gold); display: block; }
  .headline .line-sage { color: var(--sage); display: block; }

  .services {
    position: absolute; left: 158px; top: 127px; display: flex; align-items: center;
  }
  .service { display: flex; align-items: center; gap: 6px; color: var(--ink); font-size: 15px; line-height: 15px; white-space: nowrap; }
  .service svg { flex: none; }
  .service-divider { width: 1px; height: 30px; background: #888; margin: 0 18px; }

  .brand-name {
    position: absolute; left: 640px; top: 30px; width: 140px;
    text-align: center; font-family: "Marcellus", serif; font-size: 19px; line-height: 22px;
    color: var(--gold);
  }

  .band {
    position: absolute; left: 0; top: 178px; width: 100%; height: 73px; background: var(--gold);
    z-index: 1;
  }
  .band-tagline {
    position: absolute; left: 29px; top: 18px; font-size: 17px; line-height: 19px; color: var(--ink);
  }
  .band-divider { position: absolute; left: 208px; top: 21px; width: 1px; height: 32px; background: #6e5a22; }
  .phone-badge { position: absolute; left: 223px; top: 17px; width: 39px; height: 39px; }
  .phone-number {
    position: absolute; left: 271px; top: 6px;
    font-family: "Cinzel", serif; font-weight: 700; font-size: 53px; line-height: 58px; color: var(--ink);
    letter-spacing: -1px; white-space: nowrap;
  }

  .scan {
    position: absolute; z-index: 2;
    border: 5px solid var(--frame); box-shadow: 0 3px 8px rgba(0,0,0,.3);
  }
  .scan-mono {
    left: 624px; top: 107px; width: 92px; height: 118px; transform: rotate(12deg);
    background: radial-gradient(circle at 50% 45%, #6d6d6d 0%, #2a2a2a 55%, #0f0f0f 100%);
  }
  .scan-render {
    left: 695px; top: 102px; width: 114px; height: 122px; transform: rotate(-10deg);
    z-index: 3;
    background: radial-gradient(circle at 45% 50%, #c47a62 0%, #9a5443 50%, #5a2e24 100%);
  }
</style>
</head>
<body>
  <section class="billboard" aria-label="4D Cradle Glimpse billboard">
    <div class="headshot" role="img" aria-label="Professional headshot of the studio owner"></div>

    <h1 class="headline">
      <span class="line-gold">MEET YOUR BABY</span>
      <span class="line-sage">BEFORE BIRTH</span>
    </h1>

    <div class="services">
      <div class="service">
        <svg width="38" height="28" viewBox="0 0 38 28" aria-hidden="true">
          <rect x="1" y="3" width="24" height="16" rx="2" fill="var(--sage)"/>
          <rect x="4" y="6" width="18" height="10" fill="#fff"/>
          <path d="M7 14 q6 -8 12 0" fill="none" stroke="var(--sage)" stroke-width="2"/>
          <rect x="10" y="19" width="6" height="5" fill="var(--sage)"/>
          <rect x="6" y="24" width="14" height="2" fill="var(--sage)"/>
          <rect x="29" y="6" width="5" height="9" rx="2" fill="var(--sage)"/>
          <path d="M31.5 15 v9 h-8" fill="none" stroke="var(--sage)" stroke-width="1.5"/>
        </svg>
        <span>4D<br>Ultrasound</span>
      </div>
      <span class="service-divider"></span>
      <div class="service">
        <svg width="42" height="28" viewBox="0 0 42 28" aria-hidden="true">
          <circle cx="10" cy="17" r="7" fill="none" stroke="var(--sage)" stroke-width="3"/>
          <path d="M10 10 V2 M6 5 L10 1 L14 5" fill="none" stroke="var(--sage)" stroke-width="2.5"/>
          <circle cx="29" cy="10" r="7" fill="none" stroke="var(--sage)" stroke-width="3"/>
          <path d="M29 17 V27 M24 22 H34" fill="none" stroke="var(--sage)" stroke-width="2.5"/>
        </svg>
        <span>Early<br>Gender</span>
      </div>
      <span class="service-divider"></span>
      <div class="service">
        <svg width="30" height="30" viewBox="0 0 30 30" aria-hidden="true">
          <rect x="3" y="2" width="7" height="18" rx="3" fill="none" stroke="var(--sage)" stroke-width="2"/>
          <rect x="5.5" y="6" width="2" height="5" fill="var(--sage)"/>
          <path d="M6.5 20 v8" stroke="var(--sage)" stroke-width="2"/>
          <circle cx="20" cy="9" r="7" fill="none" stroke="var(--sage)" stroke-width="2"/>
          <path d="M16.5 9 l2.5 2.5 l4.5 -5" fill="none" stroke="var(--sage)" stroke-width="2"/>
          <circle cx="14" cy="24" r="1.2" fill="var(--sage)"/>
          <circle cx="17" cy="28" r="1.2" fill="var(--sage)"/>
        </svg>
        <span>Pregnancy<br>Confirmation</span>
      </div>
    </div>

    <p class="brand-name">4D Cradle<br>Glimpse</p>

    <div class="band">
      <p class="band-tagline">Private Prenatal<br>Ultrasound Studio</p>
      <span class="band-divider"></span>
      <svg class="phone-badge" viewBox="0 0 40 40" aria-hidden="true">
        <circle cx="20" cy="20" r="20" fill="var(--sage)"/>
        <path d="M13 11 l4 -1 l3 6 l-3 2 q2 5 6 7 l2 -3 l6 3 l-1 4 q-2 2 -5 1 q-10 -4 -14 -14 q-1 -3 2 -5z" fill="#fff"/>
        <path d="M23 11 q6 1 7 7 M23 15 q2 1 3 3" fill="none" stroke="#fff" stroke-width="1.6"/>
      </svg>
      <p class="phone-number">850-471-5923</p>
    </div>

    <div class="scan scan-mono" role="img" aria-label="Black and white 2D ultrasound scan"></div>
    <div class="scan scan-render" role="img" aria-label="Warm-toned 4D ultrasound image"></div>
  </section>
</body>
</html>
```